Blow Dry Bar Business Cards

These cards must be eye catching and modern.
You must be willing to work fast and make changes.

Winner will be offered other projects

Files 1 THIS IS THE STYLE CARDS I AM INTRESTED IN!!!
Please be creative, I am paying for my own eye catching design. I need files to be nexa press ready.

COLORS THAT ARE PAINTED INSIDE MY SHOP:
- - - http://www.quorvelpaint.example/en/explore-colors/painter/color-selector.html?colors=4007-3C

- - - http://www.brandivex.example/color/paint-colors/hidden-corridor-d58-2

I want the business cards sleek and modern if you use the logo please correct imperfections. I added the part that says Blow Dry Bar (see website).
Do not be afraid to separate the blow dryer from the name to make the cards look like the file with the pink elephant.

SHOULD INCLUDE
*Blow Dryer (we are a blow dry bar not a salon we do not cut or color so do not include sheers of any kind)
*BUSINESS NAME: Simply Swept Upward - Blow Dry Bar (PLEASE SEE MY WEBSITE)
* Website: SIMPLYSWEPTUPWARD.EXAMPLE
*Phone number (555) 014-2763
Updates

Nexa press said it can be submitted in JPG

http://www.brandivex.example/color/paint-colors/hidden-corridor-d58-2 http://www.quorvelpaint.example/en/explore-colors/painter/color-selector.html?colors=4007-3C ^^^^ These links will take you to the color paint that is painted inside my shop.

Target Market(s)

AGES 18 - 55 WOMEN
HIGH END MARKET

Industry/Entity Type

Salon

Requirements
Must have
• SEE COLOR EXAMPLE FILE
BLOW DRYER
UNIQUE
I LIKE THE CARD WITH THE PINK ELEPHANT THE BEST
Nice to have
• BE AS CREATIVE AND MODERN AS POSSIBLE DO NOT COPY ANY OF THE CARDS BELOW.
Should not have
• SCISSORS
PINK

```html
<!DOCTYPE html>
<html lang="en">
<head>
<meta charset="utf-8">
<title>Swept Upward – Blow Dry Bar Business Card</title>
<link rel="stylesheet" href="https://fonts.googleapis.com/css2?family=Josefin+Sans:wght@400&family=Josefin+Slab:wght@600&display=swap">
<style>
  :root {
    --ink: #1e1e1e;
    --cream: #fbe696;
    --gold: #f3dc88;
    --rule: #7d7356;
    --backdrop: #e9e6e0;
  }
  * { margin: 0; padding: 0; box-sizing: border-box; }
  html, body { width: 1200px; height: 848px; overflow: hidden; background: var(--backdrop); }
  .canvas { position: relative; width: 1200px; height: 848px; }
  .card {
    position: absolute; left: 75px; top: 124px;
    width: 1050px; height: 600px;
    border-radius: 34px; overflow: hidden;
    background: var(--ink);
    display: grid; grid-template-rows: 180px 270px 150px;
  }
  .band-top { position: relative; }
  .brand {
    position: absolute; right: 130px; top: 44px;
    display: flex; align-items: center; gap: 26px;
  }
  .brand-name {
    font-family: "Josefin Slab", serif; font-weight: 600;
    font-size: 96px; line-height: 1; color: var(--gold); white-space: nowrap;
  }
  .brand-dot { width: 64px; height: 64px; border-radius: 50%; background: var(--gold); flex: none; }
  .band-middle {
    background: var(--cream);
    display: grid; grid-template-columns: 480px 1px 1fr; align-items: center;
  }
  .tagline {
    font-family: "Josefin Slab", serif; font-weight: 600;
    font-size: 62px; line-height: 1; color: var(--ink);
    padding-left: 80px; white-space: nowrap;
  }
  .divider { width: 1px; height: 180px; background: var(--rule); }
  .contact { list-style: none; padding-left: 34px; display: grid; gap: 18px; }
  .contact li {
    display: flex; align-items: center; gap: 16px;
    font-family: "Josefin Sans", sans-serif; font-size: 23px; line-height: 1;
    color: var(--ink); letter-spacing: 0.3px; white-space: nowrap;
  }
  .contact svg { width: 32px; height: 32px; flex: none; }
  .band-bottom { display: flex; align-items: center; justify-content: center; padding: 0 40px; }
  .address {
    font-family: "Josefin Sans", sans-serif; font-size: 29px;
    color: var(--gold); letter-spacing: 0.5px; white-space: nowrap;
  }
</style>
</head>
<body>
<div class="canvas">
  <article class="card">
    <header class="band-top">
      <div class="brand">
        <span class="brand-name">Swept Upward</span>
        <span class="brand-dot"></span>
      </div>
    </header>
    <section class="band-middle">
      <h1 class="tagline">Blow Dry Bar</h1>
      <span class="divider"></span>
      <ul class="contact">
        <li>
          <svg viewBox="0 0 36 36" aria-hidden="true"><rect width="36" height="36" rx="4" fill="#1e1e1e"/><path d="M11 8c2 0 3 4 3 5s-2 2-2 3c1 3 4 6 7 7 1 0 2-2 3-2s5 1 5 3-2 4-4 4C15 28 8 21 8 12c0-2 1-4 3-4z" fill="#fbe696"/></svg>
          (555) 014-2763
        </li>
        <li>
          <svg viewBox="0 0 36 36" aria-hidden="true"><rect width="36" height="36" rx="4" fill="#1e1e1e"/><circle cx="18" cy="18" r="11" fill="none" stroke="#fbe696" stroke-width="2"/><ellipse cx="18" cy="18" rx="5" ry="11" fill="none" stroke="#fbe696" stroke-width="2"/><path d="M7 18h22M9 12h18M9 24h18" stroke="#fbe696" stroke-width="2"/></svg>
          SIMPLYSWEPTUPWARD.EXAMPLE
        </li>
        <li>
          <svg viewBox="0 0 36 36" aria-hidden="true"><rect x="3" y="8" width="30" height="20" fill="none" stroke="#1e1e1e" stroke-width="2.5"/><path d="M3 8l15 12L33 8M3 28l11-10M33 28L22 18" fill="none" stroke="#1e1e1e" stroke-width="2.5"/></svg>
          INFO@SIMPLYSWEPTUPWARD.EXAMPLE
        </li>
      </ul>
    </section>
    <footer class="band-bottom">
      <p class="address">280 HARBOR WILLOW LANE SUITE 7 BAYFIELD, TEXAS 77000</p>
    </footer>
  </article>
</div>
</body>
</html>
```